Business card por a urban DJ, up scale audience target

Need a sober design, modern, conservative colors but i can consider some options, y play rnb, hip hop, EDM and top40.

Business card for contact and personal info, double sided, use logo attrached please; im 42 so i need a card acording to my age an target audience.

Target Market(s)

Adult people, up scale audience

Industry/Entity Type

Music Download

Contact Information for Business Card

Cel (318) 4207265518 www.lumadrift.com

Requirements
Must have
• open mind
Nice to have
• open mind
Should not have
• DJ

```html
<!DOCTYPE html>
<html lang="en">
<head>
<meta charset="utf-8">
<title>Luma – Business Card</title>
<link rel="stylesheet" href="https://fonts.googleapis.com/css2?family=Arimo:wght@400;700&display=swap">
<style>
  :root {
    --page-bg: #e9e7e3;
    --card-white: #ffffff;
    --card-white-shade: #e4e4e4;
    --card-black: #1b1b1b;
    --card-black-gloss: #3a3a3a;
    --ink-dark: #1e1e1e;
    --ink-mid: #3b3b3b;
    --ink-soft: #8a8a8a;
    --ink-light: #d8d8d8;
  }
  * { box-sizing: border-box; margin: 0; padding: 0; }
  html, body { width: 1200px; height: 950px; overflow: hidden; }
  body {
    background: var(--page-bg);
    font-family: "Arimo", Arial, sans-serif;
    display: flex;
    flex-direction: column;
    align-items: center;
    justify-content: center;
    gap: 50px;
  }
  .card {
    width: 700px;
    height: 400px;
    position: relative;
    box-shadow: 0 10px 30px rgba(0,0,0,0.25);
    overflow: hidden;
  }
  /* Back side */
  .card--back {
    background: linear-gradient(90deg, var(--card-black) 0%, var(--card-black) 72%, var(--card-black-gloss) 80%, var(--card-black) 90%);
    display: flex;
    flex-direction: column;
    align-items: center;
    justify-content: center;
    gap: 18px;
  }
  .back__brand {
    font-weight: 700;
    font-size: 120px;
    letter-spacing: 6px;
    color: var(--ink-light);
    line-height: 1;
  }
  .back__web {
    font-weight: 400;
    font-size: 20px;
    letter-spacing: 3px;
    color: var(--ink-light);
  }
  /* Front side */
  .card--front {
    background: linear-gradient(160deg, var(--card-white) 0%, var(--card-white) 55%, var(--card-white-shade) 100%);
  }
  .front__brand {
    position: absolute;
    left: 60px;
    top: 48px;
    font-weight: 700;
    font-size: 78px;
    letter-spacing: 3px;
    color: var(--ink-dark);
    line-height: 1;
  }
  .front__contact {
    position: absolute;
    left: 60px;
    top: 230px;
    list-style: none;
    display: flex;
    flex-direction: column;
    gap: 8px;
  }
  .contact__item {
    display: flex;
    align-items: center;
    gap: 10px;
    font-size: 19px;
    color: var(--ink-mid);
  }
  .contact__icon { width: 16px; height: 18px; flex: none; }
  .front__person {
    position: absolute;
    right: 60px;
    bottom: 50px;
    text-align: left;
  }
  .person__name {
    font-weight: 700;
    font-size: 22px;
    letter-spacing: 1px;
    color: var(--ink-mid);
  }
  .person__role {
    font-weight: 400;
    font-size: 19px;
    letter-spacing: 1px;
    color: var(--ink-soft);
    margin-top: 2px;
  }
</style>
</head>
<body>
  <section class="card card--back" aria-label="Card back">
    <div class="back__brand">LUMA</div>
    <div class="back__web">LUMADRIFT.COM</div>
  </section>

  <section class="card card--front" aria-label="Card front">
    <div class="front__brand">LUMA</div>
    <ul class="front__contact">
      <li class="contact__item">
        <svg class="contact__icon" viewBox="0 0 16 18" aria-hidden="true">
          <rect x="3" y="1" width="10" height="16" rx="2" fill="none" stroke="var(--ink-dark)" stroke-width="2"/>
          <rect x="5" y="3.5" width="6" height="9" fill="var(--ink-dark)"/>
        </svg>
        <span>(318) 4207265518</span>
      </li>
      <li class="contact__item">
        <svg class="contact__icon" viewBox="0 0 16 18" aria-hidden="true">
          <circle cx="8" cy="9" r="7" fill="var(--ink-dark)"/>
          <path d="M1 9h14M8 2c-3 3-3 11 0 14M8 2c3 3 3 11 0 14" fill="none" stroke="var(--card-white)" stroke-width="1.2"/>
        </svg>
        <span>www.lumadrift.com</span>
      </li>
    </ul>
    <div class="front__person">
      <div class="person__name">MARCO VELL</div>
      <div class="person__role">PRESIDENT</div>
    </div>
  </section>
</body>
</html>
```